Emerging automotive detailing business

I am starting a small automotive detailing business in hopes of becoming a well-known detailer to work on high end cars. I would like a card to reflect the high quality and time I put into my work. The name of the company is Bright Crest Detailing. I feel like it represents racecars getting off the line at the drag strip as well as an innuendo of "Up the Ladder". I do minor paint correction such as clay barring, multi-step buffing and polishing, waxing, hand washes, etc. I am always striving to learn more and improve my work. My goal is to have total customer satisfaction. This is a female run business but I do not want it to be very girly. Elegant is okay! I have pictures of my personal wrenfield attached, they do not need to be incorporated but if you can think of a cool way to use 1 or all of them, go for it!

Target Market(s)

Anyone that owns a vehicle. Preferably high end vehicles such as Valtori, Castellverde and Morvani but I will also happily work on any car, truck or suv no matter what brand.

Industry/Entity Type

Automotive

Contact Information for Business Card

Bright Crest Detailing
Mira Tolland
4175 Quenhollow Rd
Ashmere PA 17492
Cell phone- call/text- 717-555-0148
email- brightcrestdetails@maildrop-example.com
Instagram: @brightcrestdetailing
Facebook: facebook.com/brightcrestdetailing

Requirements
Must have
• Business name, my name, address, phone number. Listing that I do minor paint correction such as clay barring, multi-step buffing and polishing, waxing, hand washes, interior cleaning, and more. (This last part was in nice to haves but I have realized that I do really want it, so I moved it to must haves.) I want something that is different and eye-catching to my customers. Some people have done this very well with cards already submitted to me, but a lot have not. I didn't mess with the "look and feel bars" much because because I am pretty open to the overall design as long as it is not your basic run of the mill design.
Nice to have
• Something car related. Maybe an appointment time/date line. I do not have a logo, but if you would like to design one and incorporate it, that would be amazing!
Should not have
• Purple and Pink colors. Boring, basic, normal card.

```html
<!DOCTYPE html>
<html lang="en">
<head>
<meta charset="utf-8">
<title>Bright Crest Detailing – Business Card</title>
<link rel="stylesheet" href="https://fonts.googleapis.com/css2?family=Open+Sans:wght@400;600;700;800&display=swap">
<style>
  :root {
    --stage: #e8e5e1;
    --card: #ffffff;
    --ink: #111111;
    --text: #222222;
    --red: #d9221f;
    --blue: #1d8fd6;
    --black: #141414;
    --muted: #8a8f94;
  }
  * { margin: 0; padding: 0; box-sizing: border-box; }
  html, body { width: 1200px; height: 1000px; overflow: hidden; }
  body {
    background: var(--stage);
    font-family: "Open Sans", Arial, sans-serif;
    position: relative;
  }
  .card {
    position: absolute;
    background: var(--card);
    overflow: hidden;
    box-shadow: 0 4px 14px rgba(0,0,0,0.25);
  }
  /* Front */
  .card-front { left: 45px; top: 45px; width: 732px; height: 438px; }
  .brand-name {
    position: absolute;
    font-weight: 800;
    color: var(--red);
    letter-spacing: 0.2px;
    white-space: nowrap;
  }
  .card-front .brand-name { left: 37px; top: 118px; font-size: 19px; }
  .services {
    position: absolute;
    right: 35px; top: 54px;
    width: 330px;
    text-align: center;
    font-weight: 700;
    font-size: 15px;
    line-height: 23px;
    color: var(--ink);
    text-transform: uppercase;
  }
  .services .dot { color: var(--red); }
  .person-name {
    position: absolute;
    right: 37px; top: 250px;
    font-size: 26px; font-weight: 700;
    color: var(--red);
  }
  .divider {
    position: absolute;
    left: 37px; top: 288px;
    width: 658px; height: 3px;
    background: var(--ink);
  }
  .contact {
    position: absolute;
    display: flex; align-items: center; gap: 9px;
    font-size: 19px; color: var(--text);
  }
  .contact svg { width: 20px; height: 20px; flex: none; }
  .contact-phone { left: 37px; top: 303px; }
  .contact-mail { left: 37px; top: 336px; font-size: 18px; }
  .address {
    position: absolute;
    right: 37px; top: 305px;
    text-align: right;
    font-size: 18px; line-height: 27px;
    color: var(--text);
  }
  .address svg { width: 20px; height: 18px; vertical-align: -2px; margin-right: 4px; }
  .footer-band {
    position: absolute; left: 0; bottom: 0;
    width: 100%; height: 26px;
    background: var(--black);
  }
  .social-tab {
    position: absolute;
    right: 3px; bottom: 13px;
    width: 290px; height: 33px;
    background: var(--red);
    clip-path: polygon(16px 0, 100% 0, 100% 100%, 0 100%);
    display: flex; align-items: center; justify-content: flex-end;
    padding-right: 34px; gap: 8px;
    color: #fff; font-size: 18px;
  }
  .social-tab .mark { width: 16px; height: 16px; background: #fff; opacity: 0.85; border-radius: 3px; }
  /* Back */
  .card-back { left: 407px; top: 517px; width: 731px; height: 438px; }
  .photo {
    position: absolute; inset: 0;
    background:
      radial-gradient(ellipse 300px 140px at 430px 230px, #f1d21a 0%, #e6c514 55%, rgba(230,197,20,0) 100%),
      linear-gradient(180deg, #d9dde0 0%, #aab1b6 30%, #6f767c 55%, #a9adb1 80%, #8c9094 100%);
  }
  .appointment-band {
    position: absolute; left: 0; top: 336px;
    width: 100%; height: 82px;
    background: linear-gradient(90deg, rgba(255,255,255,0.55) 0%, rgba(255,255,255,0.95) 35%, #f2f2f2 100%);
  }
  .card-back .brand-name { left: 40px; top: 397px; font-size: 14px; }
  .appointment-label {
    position: absolute; left: 485px; top: 349px;
    font-size: 16px; font-weight: 700; color: var(--ink);
  }
  .appointment-line {
    position: absolute; left: 433px; top: 399px;
    width: 270px; height: 1.5px; background: #333;
  }
</style>
</head>
<body>
  <section class="card card-front" aria-label="Business card front">
    <div class="brand-name">BRIGHT CREST DETAILING</div>
    <p class="services">
      Clay Barring <span class="dot">•</span> Multi-Step Buffing<br>
      and Polishing <span class="dot">•</span><br>
      Waxing <span class="dot">•</span> Hand Washes and More
    </p>
    <div class="person-name">Mira Tolland</div>
    <div class="divider"></div>
    <div class="contact contact-phone">
      <svg viewBox="0 0 20 20" aria-hidden="true"><circle cx="10" cy="10" r="8.5" fill="none" stroke="#1d8fd6" stroke-width="1.4"/><path d="M7 5.5l1.6 2.2-1 1.1c.6 1.3 1.5 2.2 2.7 2.8l1.1-1 2.1 1.5-.8 1.7c-3.2-.3-6-3.1-6.4-6.5z" fill="#1d8fd6"/></svg>
      <span>717-555-0148</span>
    </div>
    <div class="contact contact-mail">
      <svg viewBox="0 0 20 20" aria-hidden="true"><rect x="1.5" y="4" width="17" height="12" fill="none" stroke="#1d8fd6" stroke-width="1.4"/><path d="M1.5 4.5l8.5 6.5 8.5-6.5" fill="none" stroke="#1d8fd6" stroke-width="1.4"/></svg>
      <span>brightcrestdetails@maildrop-example.com</span>
    </div>
    <div class="address">
      <div><svg viewBox="0 0 20 18" aria-hidden="true"><path d="M10 1L1 9h3v8h4.5v-5h3v5H16V9h3z" fill="#1d8fd6"/></svg>4175 Quenhollow Rd</div>
      <div>Ashmere PA 17492</div>
    </div>
    <div class="footer-band"></div>
    <div class="social-tab"><span class="mark"></span><span>@brightcrestdetailing</span></div>
  </section>

  <section class="card card-back" aria-label="Business card back">
    <div class="photo" role="img" aria-label="Photo of a yellow sports coupe with a black hood stripe at a car show"></div>
    <div class="appointment-band"></div>
    <div class="brand-name">BRIGHT CREST DETAILING</div>
    <div class="appointment-label">APPOINTMENT TIME</div>
    <div class="appointment-line"></div>
  </section>
</body>
</html>
```